Landing Page & Email Signature

I am looking for a new landing page as well as an email signature to align with the change in business. I have included the new logo/emblem which I'd like incorporated into the design and the current landing page is www.delmorquivex.com.au should you wish to see the old version.

```html
<!DOCTYPE html>
<html lang="en">
<head>
<meta charset="utf-8">
<title>Delmor Transport &amp; Logistics</title>
<link href="https://fonts.googleapis.com/css2?family=Audiowide&family=Roboto:wght@400;500;700&display=swap" rel="stylesheet">
<style>
:root{
  --red:#b3122a;
  --red-dark:#8e0d20;
  --ink:#2a2c2f;
  --text:#555a60;
  --grey:#eef0f3;
  --line:#d9dce0;
  --white:#fff;
  --display:'Audiowide',sans-serif;
  --body:'Roboto',sans-serif;
}
*{box-sizing:border-box;margin:0;padding:0}
html,body{width:1200px;height:4357px;overflow:hidden}
body{font-family:var(--body);color:var(--text);background:var(--white);position:relative}
.abs{position:absolute}
a{color:inherit;text-decoration:none}

/* top bar */
.topbar{top:0;left:0;width:1200px;height:44px;background:var(--ink);color:#fff;font-size:13px;font-weight:500}
.topbar .contacts{left:110px;top:0;height:44px;display:flex;align-items:center;gap:14px}
.topbar .dot{width:9px;height:9px;border-radius:50%;background:var(--red);display:inline-block;margin-right:8px}
.topbar .login{left:816px;width:384px;height:44px;background:var(--red);display:flex;align-items:center;padding-left:52px;gap:16px}
.soc{width:10px;height:10px;border-radius:50%;border:2px solid #fff;display:inline-block}

/* header */
.header{top:44px;left:0;width:1200px;height:85px;background:#fff}
.brand{left:110px;top:28px;font-family:var(--body);font-weight:700;font-size:26px;color:var(--red);letter-spacing:1px;display:flex;align-items:center;gap:10px}
.brand .mark{width:22px;height:22px;border-radius:50%;background:var(--red)}
.nav{right:110px;top:0;height:85px;display:flex;gap:31px;font-size:14px;font-weight:500;color:var(--ink)}
.nav a{display:flex;align-items:center;height:85px}
.nav a.active{color:var(--red);border-bottom:3px solid var(--red)}

/* hero */
.hero{top:129px;left:0;width:1200px;height:660px;overflow:hidden}
.hero .photo{inset:0;background:linear-gradient(180deg,#8f8aa3 0%,#d9a27b 38%,#e7a460 55%,#8c6847 75%,#3a3a3c 100%)}
.hero h1{left:112px;top:173px;font-family:var(--display);font-size:38px;line-height:44px;color:var(--red);font-weight:400;text-transform:uppercase}
.hero h1 span{color:var(--ink)}
.hero p{left:112px;top:270px;width:420px;font-size:18px;font-weight:500;color:#1d1d1d;line-height:27px}
.btn-red{background:var(--red);color:#fff;font-size:13px;font-weight:700;border-radius:26px;display:flex;align-items:center;justify-content:center}
.hero .btn-red{left:112px;top:346px;width:140px;height:52px}
.arrow{width:22px;height:44px;background:#fff;display:flex;align-items:center;justify-content:center;top:265px}

/* headings */
.sec-title{font-family:var(--display);font-size:34px;color:var(--ink);text-align:center;width:1200px;left:0;font-weight:400;text-transform:uppercase}
.sec-title .r{color:var(--red)}
.lead{left:130px;width:940px;text-align:center;font-size:14px;line-height:26px}
.btn-line{border:2px solid var(--red);border-radius:26px;color:var(--ink);font-size:13px;font-weight:700;display:flex;align-items:center;justify-content:center;width:140px;height:50px;background:transparent}

/* about */
.about{top:745px;left:0;width:1200px;height:358px}
.about .ghost{left:320px;top:120px;width:560px;text-align:center;font-family:var(--body);font-weight:700;font-size:110px;color:rgba(179,18,42,.07)}

/* services */
.services{top:1103px;left:0;width:1200px;height:1122px;background:var(--grey)}
.svc h3{font-family:var(--display);font-size:24px;color:var(--ink);font-weight:400;display:flex;align-items:center;gap:18px;text-transform:uppercase}
.svc h3::after{content:"";width:56px;height:2px;background:var(--red)}
.svc p{font-size:14px;line-height:25.5px;text-align:justify;margin:20px 0 28px}
.badge{width:88px;height:88px;border-radius:50%;background:var(--red);border:5px solid #fff;display:flex;align-items:center;justify-content:center}

/* why */
.why{top:2225px;left:0;width:1200px;height:477px;background:linear-gradient(180deg,#b3122a,#9d1024 60%,#b01a30)}
.why .sec-title{color:#fff}
.card{top:149px;width:232px;height:254px;background:#fff;text-align:center;padding-top:26px}
.card h4{font-size:16px;font-weight:700;color:var(--ink);margin:14px 0 12px}
.card p{font-size:13px;line-height:24px;padding:0 10px}

/* news */
.news{top:2702px;left:0;width:1200px;height:702px}
.ncard{top:178px;width:310px;height:426px;border:1px solid var(--line)}
.ncard .pic{height:213px}
.ncard h5{font-size:17px;font-weight:500;color:var(--ink);line-height:26px;padding:12px 10px 0}
.ncard p{font-size:13px;line-height:24px;padding:10px 10px 0}
.ncard p b{color:var(--red)}
.ncard .date{position:absolute;bottom:0;left:0;right:0;height:44px;border-top:1px solid var(--line);display:flex;align-items:center;padding-left:12px;font-size:13px;gap:10px}
.ncard .date i{width:11px;height:11px;background:var(--red);display:inline-block;border-radius:2px}

/* contact */
.contact{top:3404px;left:0;width:1200px;height:674px;background:linear-gradient(180deg,#eceef1,#dfe1e4 60%,#cfd2d6)}
.crow{top:130px;left:0;width:1200px;display:flex;justify-content:center;gap:42px;font-size:16px;font-weight:500;color:var(--ink)}
.crow span{display:flex;align-items:center;gap:14px}
.ic{width:36px;height:36px;border-radius:50%;background:var(--red);display:flex;align-items:center;justify-content:center}
.field{background:#fff;border:1px solid var(--line);font-size:13px;color:#777;padding:14px 14px}

/* footer */
.footer{top:3976px;left:0;width:1200px;height:381px}
.fcol{top:154px;color:#fff;font-size:13px}
.fcol h6{font-size:15px;font-weight:700;margin-bottom:18px;color:#fff}
.fcol li{list-style:none;line-height:25px;color:#ddd}
.fcol li::before{content:"»";margin-right:14px}
.fcol p{color:#ddd;line-height:21px}
.sub{margin-top:26px;display:flex;width:270px;height:42px}
.sub span{flex:1;background:#fff;border-radius:21px 0 0 21px;color:#333;font-size:12px;display:flex;align-items:center;padding-left:14px}
.sub i{width:42px;background:var(--red);border-radius:0 21px 21px 0}
.addr li::before{content:"";display:inline-block;width:8px;height:8px;background:var(--red);border-radius:50%;margin-right:14px}
.addr li.cont::before{background:transparent}
.copy{top:346px;left:0;width:1200px;text-align:center;color:#ddd;font-size:13px}
</style>
</head>
<body>

<div class="abs topbar">
  <div class="abs contacts"><span><i class="dot"></i>+61400123987</span><span>|</span><span><i class="dot"></i>delmorlogistics@mailbox.com</span></div>
  <div class="abs login"><span>CUSTOMER LOGIN</span><span>|</span><i class="soc"></i><i class="soc"></i></div>
</div>

<header class="abs header">
  <div class="abs brand"><i class="mark"></i>DELMOR</div>
  <nav class="abs nav">
    <a class="active">HOME</a><a>ABOUT</a><a>SERVICES</a><a>WHY CHOOSE DELMOR</a><a>RESOURCES</a><a>CONTACT</a>
  </nav>
</header>

<section class="abs hero">
  <div class="abs photo" role="img" aria-label="Red semi-trailer truck on a desert highway at sunset"></div>
  <h1 class="abs">Delmor Transport<br><span>and Logistics</span></h1>
  <p class="abs">Lorem ipsum dolor sit amet, consectetur adipis cing elit, sed do eiusmod tempea.</p>
  <a class="abs btn-red">GET STARTED</a>
  <div class="abs arrow" style="left:0"><svg width="10" height="14"><path d="M8 1 2 7l6 6" stroke="#b3122a" stroke-width="2" fill="none"/></svg></div>
  <div class="abs arrow" style="right:0"><svg width="10" height="14"><path d="M2 1l6 6-6 6" stroke="#b3122a" stroke-width="2" fill="none"/></svg></div>
  <svg class="abs" style="left:0;bottom:0" width="1200" height="200" viewBox="0 0 1200 200">
    <path d="M0 200 C250 10 700 40 1200 120 L1200 200Z" fill="#b3122a"/>
    <path d="M0 200 C260 40 700 60 1200 150 L1200 200Z" fill="#fff"/>
  </svg>
</section>

<section class="abs about">
  <div class="abs ghost">DELMOR</div>
  <h2 class="abs sec-title" style="top:28px">About <span class="r">Delmor</span></h2>
  <p class="abs lead" style="top:92px">At vero eos et accusamus et iusto odio dignissimos ducimus qui blanditiis praesentium voluptatum deleniti atque corrupti quos dolores et quas molestias excepturi sint occaecati cupiditate non provident, similique sunt in culpa qui officia deserunt mollitia animi, id est laborum et dolorum fuga. Et harum quidem rerum facilis est et expedita distinctio.</p>
  <a class="abs btn-line" style="left:530px;top:210px">LEARN MORE</a>
</section>

<section class="abs services">
  <h2 class="abs sec-title" style="top:80px"><span class="r">Our</span> Services</h2>
  <p class="abs lead" style="top:147px">At vero eos et accusamus et iusto odio dignissimos ducimus qui blanditiis praesentium voluptatum deleniti atque corrupti quos dolores et quas molestias excepturi sint occaecati cupiditate non provident similique sunt in culpa qui officiea.</p>

  <div class="abs" style="left:110px;top:249px;width:489px;height:359px;background:linear-gradient(135deg,#3b3430,#c98a3a 55%,#f2c15a 70%,#5a3a2a)" role="img" aria-label="Truck speeding along a highway at sunset"></div>
  <div class="abs badge" style="left:556px;top:384px"><svg width="40" height="40" viewBox="0 0 40 40" fill="none" stroke="#fff" stroke-width="2"><circle cx="20" cy="20" r="12"/><circle cx="20" cy="20" r="4"/><path d="M20 2v10M20 28v10M2 20h10M28 20h10"/></svg></div>
  <div class="abs svc" style="left:678px;top:280px;width:410px">
    <h3>Transport</h3>
    <p>Sed ut perspiciatis unde omnis iste natus error sit voluptatem accusantium doloremque laudantium, totam rem aperiam, eaque ipsa quae ab illo inventore veritatis et quasi architecto beatae vitae dicta sunt explicabo nemo enim ipsamea. Dolor emque laudantium, totam rem aperiam, eaque ipsa quae ab illo inventore veritatis et quasi architecto.</p>
    <a class="btn-line">LEARN MORE</a>
  </div>

  <div class="abs svc" style="left:110px;top:705px;width:412px">
    <h3>Logistics</h3>
    <p>Sed ut perspiciatis unde omnis iste natus error sit voluptatem accusantium doloremque laudantium, totam rem aperiam, eaque ipsa quae ab illo inventore veritatis et quasi architecto beatae vitae dicta sunt explicabo nemo enim ipsamea. Dolor emque laudantium, totam rem aperiam, eaque ipsa quae ab illo inventore veritatis et quasi architecto.</p>
    <a class="btn-line">LEARN MORE</a>
  </div>
  <div class="abs" style="left:599px;top:674px;width:489px;height:359px;background:linear-gradient(135deg,#1e2a3a,#3a4d66 45%,#a7835a 75%,#2a2f38)" role="img" aria-label="Two workers in hard hats checking stock in a warehouse"></div>
  <div class="abs badge" style="left:556px;top:810px"><svg width="40" height="40" viewBox="0 0 40 40" fill="none" stroke="#fff" stroke-width="2"><circle cx="17" cy="17" r="12"/><path d="M5 17h24M17 5c5 6 5 18 0 24M17 5c-5 6-5 18 0 24"/><rect x="24" y="24" width="12" height="10"/></svg></div>
</section>

<section class="abs why">
  <h2 class="abs sec-title" style="top:58px">Why Choose Delmor</h2>
  <div class="abs card" style="left:110px"><svg width="48" height="48" viewBox="0 0 48 48" fill="#b3122a"><path d="M4 18 24 6l20 12v4H4z"/><rect x="8" y="24" width="32" height="20"/><rect x="14" y="30" width="20" height="14" fill="#fff"/><rect x="16" y="32" width="7" height="5"/><rect x="25" y="32" width="7" height="5"/><rect x="16" y="38" width="7" height="5"/><rect x="25" y="38" width="7" height="5"/></svg><h4>WAREHOUSING</h4><p>Lorem ipsum dolor sit amet, con sectetur adipiscing elit, sed do eiusmod tempor incididunt ut labore et dolorea.</p></div>
  <div class="abs card" style="left:359px"><svg width="48" height="48" viewBox="0 0 48 48" fill="none" stroke="#b3122a" stroke-width="3"><path d="M24 2v10M16 12h16l-8 8z"/><rect x="6" y="22" width="36" height="22"/><path d="M14 22v22M22 22v22M30 22v22M38 22v22"/></svg><h4>CARGO &amp; FREIGHT</h4><p>Lorem ipsum dolor sit amet, con sectetur adipiscing elit, sed do eiusmod tempor incididunt ut labore et dolorea.</p></div>
  <div class="abs card" style="left:607px"><svg width="48" height="48" viewBox="0 0 48 48" fill="#b3122a"><path d="M16 6l8-4 8 4v9l-8 4-8-4z"/><path d="M2 20l8 0 12 14 0 10-6 0L2 30z"/><path d="M46 20l-8 0-12 14 0 10 6 0 14-14z"/></svg><h4>HANDLING</h4><p>Lorem ipsum dolor sit amet, con sectetur adipiscing elit, sed do eiusmod tempor incididunt ut labore et dolorea.</p></div>
  <div class="abs card" style="left:856px"><svg width="70" height="48" viewBox="0 0 70 48" fill="#b3122a"><rect x="16" y="8" width="32" height="24"/><path d="M50 14h10l8 10v10H50z"/><circle cx="26" cy="38" r="6"/><circle cx="58" cy="38" r="6"/><rect x="0" y="12" width="12" height="3"/><rect x="4" y="20" width="10" height="3"/><rect x="2" y="28" width="12" height="3"/></svg><h4>SHIPMENT</h4><p>Lorem ipsum dolor sit amet, con sectetur adipiscing elit, sed do eiusmod tempor incididunt ut labore et dolorea.</p></div>
</section>

<section class="abs news">
  <h2 class="abs sec-title" style="top:86px">Latest <span class="r">News</span></h2>
  <article class="abs ncard" style="left:110px"><div class="pic" role="img" aria-label="Two lorries driving on a road at dusk" style="background:linear-gradient(180deg,#6d7a8c,#b9a07a 55%,#4b4a48)"></div><h5>Lorem ipsum dolor sit amet con ctetur adipiscing elit.</h5><p>Sed ut perspiciatis unde omnis iste natus er ror sit voluptatem accusantium dolor emq ue laudantium totam <b>Read More...</b></p><div class="date"><i></i>15 Jan 2022</div></article>
  <article class="abs ncard" style="left:445px"><div class="pic" role="img" aria-label="Warehouse worker with a tablet between tall shelves" style="background:linear-gradient(180deg,#d9d4c8,#a8896a 50%,#5c4a3a)"></div><h5>Lorem ipsum dolor sit amet con ctetur adipiscing elit.</h5><p>Sed ut perspiciatis unde omnis iste natus er ror sit voluptatem accusantium dolor emq ue laudantium totam <b>Read More...</b></p><div class="date"><i></i>15 Jan 2022</div></article>
  <article class="abs ncard" style="left:778px"><div class="pic" role="img" aria-label="Blue truck on an open road under a cloudy sky" style="background:linear-gradient(180deg,#7f93ad,#d9c49a 55%,#6a6a52)"></div><h5>Lorem ipsum dolor sit amet con ctetur adipiscing elit.</h5><p>Sed ut perspiciatis unde omnis iste natus er ror sit voluptatem accusantium dolor emq ue laudantium totam <b>Read More...</b></p><div class="date"><i></i>15 Jan 2022</div></article>
</section>

<section class="abs contact">
  <div class="abs" role="img" aria-label="Faded truck on a highway in the background" style="right:0;top:180px;width:300px;height:400px;background:linear-gradient(180deg,rgba(255,255,255,0),rgba(200,204,210,.6))"></div>
  <h2 class="abs sec-title" style="top:56px">Get in <span class="r">Touch</span></h2>
  <div class="abs crow">
    <span><i class="ic"><svg width="16" height="16" viewBox="0 0 16 16" fill="#fff"><path d="M3 1l3 3-2 2c1 2 3 4 5 5l2-2 3 3-2 3C6 14 2 10 1 3z"/></svg></i>+61400123987</span>
    <span><i class="ic"><svg width="16" height="12" viewBox="0 0 16 12"><rect width="16" height="12" fill="#fff"/><path d="M0 0l8 6 8-6" stroke="#b3122a" stroke-width="1.5" fill="none"/></svg></i>delmorlogistics@mailbox.com</span>
  </div>
  <div class="abs field" style="left:217px;top:212px;width:379px;height:47px">First Name</div>
  <div class="abs field" style="left:604px;top:212px;width:377px;height:47px">Last Name</div>
  <div class="abs field" style="left:217px;top:271px;width:379px;height:47px">Email</div>
  <div class="abs field" style="left:604px;top:271px;width:377px;height:47px">Phone</div>
  <div class="abs field" style="left:217px;top:330px;width:764px;height:105px">Enter Your Message</div>
  <a class="abs btn-red" style="left:514px;top:450px;width:170px;height:48px;font-size:14px">ENQUIRE NOW</a>
</section>

<footer class="abs footer">
  <svg class="abs" style="left:0;top:0" width="1200" height="381" viewBox="0 0 1200 381">
    <path d="M0 120 C300 10 800 -10 1200 120 L1200 381 L0 381Z" fill="#b3122a"/>
    <path d="M0 130 C300 40 800 30 1200 140 L1200 381 L0 381Z" fill="#2a2c2f"/>
  </svg>
  <div class="abs fcol" style="left:110px;width:280px"><h6>NEWSLETTER SUBSCRIBE</h6><p>Subscribe to our newsletter and we will keep you informed about us.</p><div class="sub"><span>Your Email*</span><i></i></div></div>
  <div class="abs fcol" style="left:445px"><h6>QUICK LINKS</h6><ul><li>Home</li><li>About</li><li>Services</li><li>Why Choose Delmor</li><li>Contact</li></ul></div>
  <div class="abs fcol" style="left:656px"><h6>OTHER LINKS</h6><ul><li>Resources</li><li>Privacy Policy</li><li>Terms Of Use</li><li>Legal Support</li><li>Help Center</li></ul></div>
  <div class="abs fcol addr" style="left:854px;width:240px"><h6>CONTACT DELMOR</h6><ul><li>78, Carvel Norton Street,</li><li class="cont">United States</li><li>+61400123987</li><li>delmorlogistics@mailbox.com</li></ul></div>
  <div class="abs" style="left:1122px;top:290px;width:32px;height:32px;border-radius:50%;background:var(--red);display:flex;align-items:center;justify-content:center"><svg width="12" height="8"><path d="M1 7l5-5 5 5" stroke="#fff" stroke-width="2" fill="none"/></svg></div>
  <div class="abs" style="left:1024px;top:336px;width:28px;height:28px;border-radius:50%;background:#fff"></div>
  <div class="abs" style="left:1058px;top:336px;width:28px;height:28px;border-radius:50%;background:#fff"></div>
  <div class="abs copy">© 2022 Delmor Transport &amp; Logistics | All Rights Reserved</div>
</footer>

</body>
</html>
```